Need a Zine cover designed

I’m looking for someone who can design an eye catching and original zine cover. Incorporating the logo I included below. I’m not 100% sure which logo I want to use on the cover, if it’s possible to see how you incorporate the logos on a sample will make it easier for me to decide. Thank you for your time.
For the second logo I’m unsure how to remove the grey background, but I do not want it included in the zine cover
The title of the zine is:
Marigold Crossing
perspectives of culture, life, & love

```html
<!DOCTYPE html>
<html lang="en">
<head>
<meta charset="utf-8">
<title>Marigold Crossing — Zine Cover</title>
<link rel="stylesheet" href="https://fonts.googleapis.com/css2?family=Sancreek&family=Josefin+Sans:wght@300;400;700&display=swap">
<style>
  :root {
    --backdrop: #1b1b1b;
    --paper: #ffffff;
    --ink: #1c1c1c;
    --orange: #ee5a24;
    --amber: #dcae4e;
    --lime: #cde06a;
    --mint: #7fd5ad;
    --sky: #1fc1e8;
    --leaf: #a9d67c;
  }
  * { margin: 0; padding: 0; box-sizing: border-box; }
  html, body {
    width: 1200px;
    height: 1200px;
    overflow: hidden;
    background: var(--backdrop);
  }
  .zine-cover {
    position: absolute;
    left: 290px;
    top: 120px;
    width: 620px;
    height: 960px;
    background: var(--paper);
    border: 1px solid #000;
  }
  .club-name {
    position: absolute;
    top: 88px;
    left: 0;
    width: 100%;
    text-align: center;
    font-family: "Josefin Sans", sans-serif;
    font-weight: 700;
    font-size: 30px;
    line-height: 1.1;
    letter-spacing: 2px;
    color: var(--ink);
  }
  .title-art {
    position: absolute;
    left: 0;
    top: 0;
    width: 620px;
    height: 960px;
  }
  .title-solid, .title-outline {
    font-family: "Sancreek", serif;
    font-size: 195px;
  }
  .title-outline {
    fill: none;
    stroke: var(--orange);
    stroke-width: 1;
  }
  .tagline {
    position: absolute;
    left: 39px;
    top: 858px;
    font-family: "Josefin Sans", sans-serif;
    font-weight: 300;
    font-size: 34px;
    line-height: 40px;
    letter-spacing: 2px;
    color: var(--ink);
    text-transform: uppercase;
  }
  .tagline .culture { color: var(--orange); }
  .tagline .life { color: var(--leaf); }
  .tagline .love { color: var(--sky); }
</style>
</head>
<body>
  <main class="zine-cover">
    <div class="club-name">LANTERN HOURS<br>CLUB</div>

    <svg class="title-art" viewBox="0 0 620 960" aria-label="Marigold Crossing">
      <defs>
        <linearGradient id="title-gradient" x1="28" y1="0" x2="592" y2="0" gradientUnits="userSpaceOnUse">
          <stop offset="0" stop-color="var(--orange)"/>
          <stop offset="0.3" stop-color="var(--amber)"/>
          <stop offset="0.5" stop-color="var(--lime)"/>
          <stop offset="0.75" stop-color="var(--mint)"/>
          <stop offset="1" stop-color="var(--sky)"/>
        </linearGradient>
      </defs>
      <text class="title-solid" x="28" y="498" textLength="563" lengthAdjust="spacingAndGlyphs" fill="url(#title-gradient)">MARIGOLD</text>
      <text class="title-outline" x="28" y="601" textLength="563" lengthAdjust="spacingAndGlyphs">CROSSING</text>
    </svg>

    <p class="tagline">
      Perspectives of<br>
      <span class="culture">Culture</span>, <span class="life">Life</span>, &amp; <span class="love">Love</span>
    </p>
  </main>
</body>
</html>
```